Fitness Equipment & Service

I want to make the card eye catching and fun. We are called Corvane Motion Limited and we are based in Wales. We sell, install and service all types of fitness equipment from Skipping ropes, right through the Dumbbells, Kettle bells and Barbells through to state of the art Treadmills, Running Machines and Strength Equipment. We also design and install changing room furniture and lockers.

TYPOGRAPHY
We would like to use Futrura. Futura has an appearance of efficiency and forwardness. The typeface is derived
from simple geometric forms (near-perfect circles, triangles and squares) and is based on strokes of
near-even weight, which are low in contrast. This is most visible in the almost perfectly round stroke of
the o, which is nonetheless slightly ovoid.
The lowercase has tall ascenders, which rise above the cap line. The uppercase
characters present proportions similar to those of classical Roman capitals.

TYPOGRAPHIC CONSIDERATIONS
No Strike though
No Horizontal Scaling
No Drop Shadows
No Effects
Never use less than 120% Leading

OUR CORPORATE COLOURS
BRAND GUIDELINES
We were thinking that our primary colour palette consists of the Acid Green (Pantone 382) and Process Black.

We work closely with tquarly Ltd and would like to include their name on the card somewhere. I have attached images of the other brands that we work with as an idea or the small icons I have included that illustrate what we do?. I have very kindly been given permission to use any of the images off the files that I have included below, so I hope these help. I will include these below. I would be open to suggestions if it made the card more striking Can you do it?
Updates

Hi All, Just wanted to add a few thoughts but you are the guys with the creative visions (thats why are here) We are based in Wales, UK and we would be open to lots of different ideas on a theme but must be eye catching, Bold and FUN. If you can or think that the Welsh or any dragon could be put in there then go for it (its not a must have) We have also added some ideas for colour but again its over to you!! GO FOR IT ! Thanks and look forward to your visions! Owen

Hi All, Just thought I would sen through the contact details that need to be on the card. (if you want to play around with icons instead of the wording twitter, Facebook, go for it): Corvane Motion Limited Owen Pritchard Managing Director Mob: +44 (0)7582 913 406 e-mail: sales@corvanemotion.co.uk Web: Corvanemotion.co.uk twitter: @motionLetterbin Facebook: Corvane Motion Limited

```html
<!DOCTYPE html>
<html lang="en">
<head>
<meta charset="utf-8">
<title>Corvane Motion Limited – Business Card</title>
<link href="https://fonts.googleapis.com/css2?family=Jost:wght@400;500&display=swap" rel="stylesheet">
<style>
  :root {
    --page-bg: #e6e3df;
    --navy-deep: #0c1a3c;
    --navy-mid: #1d3a78;
    --navy-light: #3a5ca6;
    --frost: #e9e8e6;
    --frost-shade: #d3d1cd;
    --gold-ring: #8a5a22;
    --name-tone: #d9d3c8;
    --text-light: #f1efeb;
    --text-soft: #c9b8b0;
    --ink: #121212;
    --emblem: #16295a;
  }
  * { margin: 0; padding: 0; box-sizing: border-box; }
  html, body {
    width: 1200px; height: 969px; overflow: hidden;
    background: var(--page-bg);
    font-family: "Jost", "Futura", sans-serif;
  }
  .business-card {
    position: absolute; left: 100px; top: 201px;
    width: 1000px; height: 567px;
    box-shadow: 0 12px 30px rgba(0,0,0,0.18);
  }
  .card-art { position: absolute; inset: 0; }
  .holder-name {
    position: absolute; left: 43px; top: 50px;
    font-size: 38px; font-weight: 500; color: var(--name-tone);
    line-height: 1.2;
  }
  .holder-title {
    position: absolute; left: 43px; top: 96px;
    font-size: 28px; font-weight: 400; color: var(--name-tone);
    line-height: 1.2;
  }
  .postal-address {
    position: absolute; left: 43px; top: 233px;
    font-style: normal; font-size: 26px; color: var(--text-light);
    line-height: 1.4;
  }
  .contact-list {
    position: absolute; left: 43px; top: 335px;
    list-style: none; font-size: 24px; color: var(--text-light);
    line-height: 1.25;
  }
  .contact-list li {
    display: flex; align-items: center; gap: 14px; height: 37.5px;
  }
  .contact-list .icon { width: 22px; height: 22px; flex: none; }
  .contact-list .social-dot {
    width: 17px; height: 17px; margin: 0 2.5px; flex: none;
    background: var(--text-light); border-radius: 2px;
  }
  .contact-list .facebook-line { color: var(--text-soft); }
  .company-name {
    position: absolute; left: 600px; top: 378px; width: 300px;
    text-align: center;
    font-size: 30px; font-weight: 500; color: var(--ink);
    line-height: 1.2;
  }
</style>
</head>
<body>
  <div class="business-card">
    <svg class="card-art" width="1000" height="567" viewBox="0 0 1000 567" aria-hidden="true">
      <defs>
        <linearGradient id="navyPanel" x1="0" y1="0" x2="1" y2="1">
          <stop offset="0" stop-color="var(--navy-mid)"/>
          <stop offset="0.45" stop-color="var(--navy-light)"/>
          <stop offset="1" stop-color="var(--navy-deep)"/>
        </linearGradient>
        <linearGradient id="frostPanel" x1="0" y1="0" x2="1" y2="1">
          <stop offset="0" stop-color="var(--frost)"/>
          <stop offset="1" stop-color="var(--frost-shade)"/>
        </linearGradient>
        <clipPath id="cardShape"><rect width="1000" height="567"/></clipPath>
      </defs>
      <g clip-path="url(#cardShape)">
        <rect width="1000" height="567" fill="url(#navyPanel)"/>
        <rect x="739" width="261" height="567" fill="url(#frostPanel)"/>
        <circle cx="739" cy="283" r="292" fill="url(#frostPanel)"/>
        <circle cx="739" cy="283" r="296" fill="none" stroke="var(--gold-ring)" stroke-width="6"/>
      </g>
      <circle class="brand-emblem" cx="747" cy="215" r="88" fill="var(--emblem)"/>
    </svg>

    <div class="holder-name">Owen Pritchard</div>
    <div class="holder-title">Managing Director</div>

    <address class="postal-address">42 Heron Quay Road<br>Cardiff, Wales CF10 4TB</address>

    <ul class="contact-list">
      <li>
        <svg class="icon" viewBox="0 0 22 22"><rect x="6" y="1" width="10" height="20" rx="2" fill="none" stroke="#f1efeb" stroke-width="2"/><circle cx="11" cy="17" r="1.3" fill="#f1efeb"/></svg>
        +44 (0)7582 913 406
      </li>
      <li>
        <svg class="icon" viewBox="0 0 22 22"><rect x="2" y="5" width="18" height="12" fill="#f1efeb"/><path d="M2 5 L11 12 L20 5" fill="none" stroke="#1d3a78" stroke-width="1.5"/></svg>
        sales@corvanemotion.co.uk
      </li>
      <li>
        <svg class="icon" viewBox="0 0 22 22"><circle cx="11" cy="11" r="9" fill="none" stroke="#f1efeb" stroke-width="2"/><ellipse cx="11" cy="11" rx="4" ry="9" fill="none" stroke="#f1efeb" stroke-width="1.5"/><line x1="2" y1="11" x2="20" y2="11" stroke="#f1efeb" stroke-width="1.5"/></svg>
        www.Corvanemotion.co.uk
      </li>
      <li><span class="social-dot"></span>@motionLetterbin</li>
      <li class="facebook-line"><span class="social-dot"></span>Corvane Motion Limited</li>
    </ul>

    <div class="company-name">Corvane Motion Limited</div>
  </div>
</body>
</html>
```